Business Card design, meridale shipping

I started a container shipping company which specialized in export of cars, motorcycles, boats and general cargo overseas. I need a business card that stands out of the pack and gives clients an idea of what I do. I have attached a sample that someone designed for me but I don't think its the right fit. However the info on it is accurate so can be used right on new card.

Reason: I would like my new logo which is being designed on KORVANTILE.COM as well to be implemented into my business card.

Shipping

```html
<!DOCTYPE html>
<html lang="en">
<head>
<meta charset="utf-8">
<title>Meridale Shipping — Business Card</title>
<link href="https://fonts.googleapis.com/css2?family=Source+Sans+3:wght@400;600;700&display=swap" rel="stylesheet">
<style>
  :root {
    --backdrop: #141616;
    --brand-blue: #0b33ea;
    --name-blue: #0a3cdc;
    --title-blue: #3a6fe6;
    --icon-blue: #2a5fe0;
    --card-white: #ffffff;
    --text-grey: #8b9292;
    --tagline-white: #dfe6ff;
  }
  * { box-sizing: border-box; margin: 0; padding: 0; }
  html, body {
    width: 1200px; height: 900px; overflow: hidden;
    background: var(--backdrop);
    font-family: "Source Sans 3", "Myriad Pro", Arial, sans-serif;
  }
  .canvas { position: relative; width: 1200px; height: 900px; }

  .card {
    position: absolute;
    border-radius: 12px;
    overflow: hidden;
  }
  .card--front {
    left: 150px; top: 307px; width: 436px; height: 252px;
    background: var(--brand-blue);
  }
  .card--back {
    left: 631px; top: 310px; width: 431px; height: 250px;
    background: var(--card-white);
  }

  .brand-lockup {
    position: absolute; left: 70px; top: 128px;
    text-align: right;
  }
  .brand-name {
    display: block;
    color: var(--card-white);
    font-weight: 600;
    font-size: 33px;
    letter-spacing: 0.2px;
    line-height: 1;
  }
  .brand-tagline {
    display: block;
    margin-top: 8px;
    color: var(--tagline-white);
    font-weight: 600;
    font-size: 8px;
    letter-spacing: 0.4px;
  }

  .back-brand {
    position: absolute; left: 22px; top: 122px;
    display: flex; align-items: center; gap: 8px;
    color: var(--name-blue);
    font-weight: 600;
    font-size: 20px;
  }
  .back-brand__dot {
    width: 12px; height: 12px; border-radius: 50%;
    background: var(--name-blue);
  }

  .contact-block { position: absolute; left: 225px; top: 46px; }
  .person-name {
    color: var(--name-blue);
    font-weight: 700;
    font-size: 19px;
    line-height: 1.1;
  }
  .person-title {
    color: var(--title-blue);
    font-size: 13px;
    line-height: 1.3;
  }
  .address {
    margin-top: 10px;
    color: var(--text-grey);
    font-size: 13px;
    line-height: 1.12;
  }
  .contact-list {
    list-style: none;
    margin-top: 12px;
  }
  .contact-list li {
    display: flex; align-items: center; gap: 8px;
    color: var(--text-grey);
    font-size: 13px;
    line-height: 16.2px;
  }
  .contact-list svg { width: 9px; height: 9px; fill: var(--icon-blue); flex: none; }
</style>
</head>
<body>
<div class="canvas">

  <section class="card card--front" aria-label="Card front">
    <div class="brand-lockup">
      <span class="brand-name">Meridale Shipping</span>
      <span class="brand-tagline">MOVING AROUND THE WORLD</span>
    </div>
  </section>

  <section class="card card--back" aria-label="Card back">
    <div class="back-brand">
      <span class="back-brand__dot"></span>
      <span>Meridale Shipping</span>
    </div>

    <div class="contact-block">
      <p class="person-name">Elias Marrow</p>
      <p class="person-title">Managing Director</p>
      <p class="address">1234, Address Goes Here<br>Country Name, 123456</p>
      <ul class="contact-list">
        <li><svg viewBox="0 0 10 10" aria-hidden="true"><path d="M3 0h4a1 1 0 0 1 1 1v8a1 1 0 0 1-1 1H3a1 1 0 0 1-1-1V1a1 1 0 0 1 1-1zm0 1.5v6h4v-6z"/></svg>123-456-7890</li>
        <li><svg viewBox="0 0 10 10" aria-hidden="true"><path d="M0 3c2-2 8-2 10 0v1.5H7.5V3.5h-5v1H0zM2 5h6l1 4H1z"/></svg>123-456-7890</li>
        <li><svg viewBox="0 0 10 10" aria-hidden="true"><path d="M2 0h5v3h2v7H1V3h1zm1 1v2h3V1zM2.5 5v1h1V5zm2 0v1h1V5zm2 0v1h1V5z"/></svg>123-456-7890</li>
        <li><svg viewBox="0 0 10 10" aria-hidden="true"><path d="M0 2h10v1L5 6 0 3zM0 4l5 3 5-3v4H0z"/></svg>info@youremail.com</li>
        <li><svg viewBox="0 0 10 10" aria-hidden="true"><path d="M6 1l3 3-2 2-1-1 1-1-1-1-2 2-1-1zM4 9L1 6l2-2 1 1-1 1 1 1 2-2 1 1z"/></svg>www.yourweb.com</li>
      </ul>
    </div>
  </section>

</div>
</body>
</html>
```